NZ First of it's kind solutions directory and marketplace for busy Mums needs a business card design

We need a business card design for our new nationwide business in NZ (long term plans to go global). We provide solutions to the everyday challenges that busy Mums face by connecting them with quality communities and suppliers of carefully selected, relevant products and services. We sell direct via our online marketplace. The final design should communicate our values of inclusivity, quality and smart solutions. Colours should incorporate our logo colour palette of #477077 and #6ba8b2. Our website is at https://www.brightnestmums.example

Target Market(s)

busy Mums, Age 28 – 50, female, income over $100K, location main centres NZ primarily but NZ wide. Is likely juggling work or career with a young family. Probably had hobbies which have fallen by the wayside.
-Wants to succeed in her chosen career without compromising on family life
-to successfully juggle her career without feeling like she is compromising her children
- Is time poor, something always has to give and it’s generally her health (she’ll stay up late, get stressed)
- probably ex corporate or professional career. Has discretional income

Industry/Entity Type

Business

Contact Information for Business Card

Lena Forbisher, Founder, BrightNestMums.example (Strapline Tap; Gather; Sorted), 47 Kowhai Terrace, Ellerslie, Auckland 1051, New Zealand. Mob: 021 483 517 Ph: +64 (0)9 571 4860

Font styles to use
Other font styles liked:
• Raleway, and/or Architects Daughter

Colors
00a990
33b8a4
86cfc6
cfeae6

Requirements
Must have
• the above details, streamline. the logo and colours associated with those logos
Should not have
• foil or metallic colours

```html
<!DOCTYPE html>
<html lang="en">
<head>
<meta charset="utf-8">
<title>BrightNestMums — Business Card</title>
<link rel="stylesheet" href="https://fonts.googleapis.com/css2?family=Roboto:wght@400;500&display=swap">
<style>
  :root {
    --backdrop: #2b2b2b;
    --brand-dark: #4a7278;
    --brand-light: #6ba8b2;
    --paper: #f1f1f1;
    --ink-white: #ffffff;
  }
  * { margin: 0; padding: 0; box-sizing: border-box; }
  html, body {
    width: 1200px; height: 960px; overflow: hidden;
    background: var(--backdrop);
    font-family: "Roboto", Arial, sans-serif;
  }
  .canvas { position: relative; width: 1200px; height: 960px; }
  .card {
    position: absolute; width: 600px; height: 342px; overflow: hidden;
    box-shadow: 0 3px 6px rgba(0,0,0,0.45);
  }
  .card-front { left: 314px; top: 113px; background: var(--paper); }
  .card-back { left: 311px; top: 472px; background: var(--brand-light); }
  .front-wave { position: absolute; inset: 0; }
  .brand-name {
    position: absolute; left: 46px; top: 76px;
    font-size: 34px; font-weight: 500; color: var(--brand-dark);
    letter-spacing: -0.5px;
  }
  .brand-dot {
    position: absolute; left: 46px; top: 84px; width: 0; height: 0;
  }
  .contact-block {
    position: absolute; right: 26px; top: 158px; text-align: right;
    color: var(--ink-white);
  }
  .person-name {
    font-size: 20px; font-weight: 400; color: var(--brand-light);
    text-transform: uppercase; letter-spacing: 0.2px; line-height: 26px;
  }
  .person-role { font-size: 15px; font-weight: 500; text-transform: uppercase; line-height: 20px; margin-bottom: 12px; }
  .contact-line {
    display: flex; justify-content: flex-end; align-items: center; gap: 6px;
    font-size: 14px; line-height: 19.5px;
  }
  .contact-icon { width: 13px; height: 13px; fill: var(--brand-light); }
  .address { font-size: 14px; line-height: 18.5px; margin-top: 6px; }
  .back-name {
    position: absolute; left: 0; right: 0; top: 140px; text-align: center;
    font-size: 40px; font-weight: 500; color: var(--ink-white);
  }
  .strapline {
    position: absolute; left: 0; right: 0; top: 305px; text-align: center;
    font-size: 14px; color: var(--ink-white);
  }
</style>
</head>
<body>
<main class="canvas">
  <section class="card card-front">
    <svg class="front-wave" width="600" height="342" viewBox="0 0 600 342" aria-hidden="true">
      <path d="M0,250 C110,318 330,300 600,20 L600,342 L0,342 Z" fill="#6ba8b2"/>
      <path d="M0,256 C120,330 340,300 600,24 L600,342 L0,342 Z" fill="#ffffff"/>
      <path d="M0,262 C130,304 350,292 600,28 L600,342 L0,342 Z" fill="#4a7278"/>
    </svg>
    <div class="brand-name">BrightNestMums</div>
    <div class="contact-block">
      <div class="person-name">Lena Forbisher</div>
      <div class="person-role">Founder</div>
      <div class="contact-line">+64 (0)9 571 4860
        <svg class="contact-icon" viewBox="0 0 16 16"><path d="M3.6 1.5l2.3 2.6-1.2 1.8c.9 2 2.5 3.6 4.5 4.5l1.8-1.2 2.6 2.3-1.3 2.2C7.4 15.2.8 8.6 1.3 2.8z"/></svg>
      </div>
      <div class="contact-line">021 483 517
        <svg class="contact-icon" viewBox="0 0 16 16"><path d="M4 0h8a1 1 0 0 1 1 1v14a1 1 0 0 1-1 1H4a1 1 0 0 1-1-1V1a1 1 0 0 1 1-1zm1 2v10h6V2zm3 11a1 1 0 1 0 0 2 1 1 0 0 0 0-2z"/></svg>
      </div>
      <div class="contact-line">BrightNestMums.example
        <svg class="contact-icon" viewBox="0 0 16 16"><circle cx="8" cy="8" r="7.5"/><path d="M4 4c2 0 2 2 3.5 2.5S7 9 5.5 9 4 11 4.5 13M10 2.5c0 2 2 1.5 2.5 3s-1 3 .5 4.5" stroke="#4a7278" stroke-width="1.2" fill="none"/></svg>
      </div>
      <div class="address">47 Kowhai Terrace, Ellerslie<br>Auckland 1051, New Zealand</div>
    </div>
  </section>

  <section class="card card-back">
    <div class="back-name">BrightNestMums</div>
    <p class="strapline">Tap; Gather; Sorted</p>
  </section>
</main>
</body>
</html>
```